Business Card Design for Software Development Company

I am looking for a business card design the incorporates my new logo (attached below).

Key information to include:
Name: Martin Quelbrook
Title: CEO
Email: martin@brightwellcivic.example
Phone: 555-218-9403
Website: www.brightwellcivic.example

NOTE: This design should be easy to edit so that we can order cards for different members of our team.

```html
<!DOCTYPE html>
<html lang="en">
<head>
<meta charset="utf-8">
<title>BrightwellLabs Business Card</title>
<link href="https://fonts.googleapis.com/css2?family=Montserrat:wght@400;500;600&display=swap" rel="stylesheet">
<style>
  :root {
    --page-bg: #2f3033;
    --card-white: #ffffff;
    --navy: #39415a;
    --ink: #333a52;
    --orange: #dd4f26;
    --white: #ffffff;
  }
  html, body {
    margin: 0;
    width: 1200px;
    height: 1059px;
    overflow: hidden;
    background: var(--page-bg);
    font-family: "Montserrat", Arial, sans-serif;
  }
  .canvas { position: relative; width: 1200px; height: 1059px; }

  .card {
    position: absolute;
    border-radius: 24px;
    overflow: hidden;
    box-shadow: 0 14px 28px rgba(0,0,0,.45);
  }

  /* Front */
  .card-front { left: 256px; top: 100px; width: 688px; height: 391px; background: var(--card-white); }
  .front-band { position: absolute; left: 0; bottom: 0; width: 688px; height: 16px; }

  .brand-front {
    position: absolute; left: 38px; top: 173px;
    display: flex; align-items: center; gap: 8px;
  }
  .brand-dot { width: 18px; height: 18px; border-radius: 50%; background: var(--orange); }
  .brand-name-front { font-size: 32px; font-weight: 600; color: var(--ink); letter-spacing: -0.5px; }
  .brand-sub-front {
    position: absolute; left: 0; right: 0; top: 44px; text-align: right;
    font-size: 5px; font-weight: 600; color: var(--ink); letter-spacing: .3px;
  }

  .divider { position: absolute; left: 345px; top: 109px; width: 1.5px; height: 173px; background: var(--ink); }

  .contact-block { position: absolute; left: 373px; top: 108px; color: var(--ink); }
  .person-name { margin: 0; font-size: 25px; font-weight: 600; letter-spacing: -0.3px; text-transform: uppercase; line-height: 1.1; }
  .person-title { margin: 2px 0 0; font-size: 17px; font-weight: 400; line-height: 1.1; }
  .rule { width: 16px; height: 1.5px; background: var(--ink); margin: 20px 0 18px; }
  .contact-list { list-style: none; padding: 0; margin: 0; }
  .contact-list li { display: flex; align-items: center; gap: 8px; font-size: 15.5px; height: 26px; letter-spacing: .2px; }
  .contact-list svg { width: 13px; height: 13px; flex: none; }

  /* Back */
  .card-back { left: 253px; top: 537px; width: 694px; height: 394px; background: var(--navy); }
  .brand-back {
    position: absolute; left: 0; right: 0; top: 155px;
    display: flex; justify-content: center; align-items: center; gap: 14px;
  }
  .brand-back .brand-dot { width: 30px; height: 30px; }
  .brand-back-inner { position: relative; }
  .brand-name-back { font-size: 58px; font-weight: 600; color: var(--white); letter-spacing: -1px; line-height: 1; }
  .brand-sub-back {
    position: absolute; right: 0; top: 64px;
    font-size: 8.5px; font-weight: 600; color: var(--white); letter-spacing: .5px; white-space: nowrap;
  }
</style>
</head>
<body>
<main class="canvas">

  <section class="card card-front" aria-label="Business card front">
    <div class="brand-front">
      <span class="brand-dot"></span>
      <div style="position:relative">
        <span class="brand-name-front">BrightwellLabs</span>
        <span class="brand-sub-front">A DIVISION OF BRIGHTWELL CIVIC</span>
      </div>
    </div>

    <div class="divider"></div>

    <div class="contact-block">
      <h1 class="person-name">Martin Quelbrook</h1>
      <p class="person-title">CEO</p>
      <div class="rule"></div>
      <ul class="contact-list">
        <li>
          <svg viewBox="0 0 24 24"><path fill="#333a52" d="M6.6 10.8a15 15 0 0 0 6.6 6.6l2.2-2.2a1 1 0 0 1 1-.25 11.4 11.4 0 0 0 3.6.57 1 1 0 0 1 1 1V20a1 1 0 0 1-1 1A17 17 0 0 1 3 4a1 1 0 0 1 1-1h3.5a1 1 0 0 1 1 1c0 1.25.2 2.45.57 3.57a1 1 0 0 1-.25 1z"/></svg>
          555-218-9403
        </li>
        <li>
          <svg viewBox="0 0 24 24"><path fill="#333a52" d="M2 5h20v14H2z"/><path fill="none" stroke="#fff" stroke-width="2" d="M2 6l10 7 10-7"/></svg>
          martin@brightwellcivic.example
        </li>
        <li>
          <svg viewBox="0 0 24 24" fill="none" stroke="#333a52" stroke-width="1.8"><circle cx="12" cy="12" r="10"/><path d="M2 12h20M12 2c3 3 3 17 0 20M12 2c-3 3-3 17 0 20"/></svg>
          www.brightwellcivic.example
        </li>
      </ul>
    </div>

    <svg class="front-band" viewBox="0 0 688 16" preserveAspectRatio="none">
      <polygon points="0,0 350,0 335,16 0,16" fill="#39415a"/>
      <polygon points="357,0 688,0 688,16 342,16" fill="#dd4f26"/>
    </svg>
  </section>

  <section class="card card-back" aria-label="Business card back">
    <div class="brand-back">
      <span class="brand-dot"></span>
      <div class="brand-back-inner">
        <span class="brand-name-back">BrightwellLabs</span>
        <span class="brand-sub-back">A DIVISION OF BRIGHTWELL CIVIC</span>
      </div>
    </div>
  </section>

</main>
</body>
</html>
```